Captivating packaging design for sports company.

We need a packaging design that encompasses our resistance bands workout set. Our focus is quality, convenience, and versatility. The design should be tailored to our broad array of customer across all paths. We would like the packaging to reflect our brand and product features such as: the LBS(weight) listed on each of the bands, convenience for travel and at home, highest quality, for all fitness levels, and free eBook. We'd also like to include a couple of our reviews on the packaging. Please refer to our listing on Varlo for additional information https://www.shopvarlo.com/Brisklane-Athletics-Resistance-Workout-Carrying/dp/K47TR2XMNQ/ref=sr_1_1?ie=UTF8&qid=1470453588&sr=8-1&keywords=brisklane+athletics+resistance+bands
Please reach out with additional questions for any further details. Thank you.
Target Market(s)
Sports, fitness, and health enthusiasts of all ages.
Industry/Entity Type
It Company
Look and feel
Each slider illustrates characteristics of the customer's brand and the style your logo design should communicate.

```html
<!DOCTYPE html>
<html lang="en">
<head>
<meta charset="utf-8">
<title>Brisklane Athletics Resistance Band Packaging</title>
<link rel="stylesheet" href="https://fonts.googleapis.com/css2?family=Archivo:wdth,wght@125,700;125,800;125,900&family=Montserrat:wght@600;700;800&display=swap">
<style>
  :root {
    --bg-top: #8d8d8d;
    --bg-bottom: #e4e4e4;
    --panel-dark: #3b3b3c;
    --panel-top: #333334;
    --orange-deep: #d9481b;
    --orange: #e8621f;
    --orange-light: #f29a2a;
    --white: #ffffff;
    --cream: #fff3d6;
    --photo-sky: #d9dfe0;
    --photo-green: #8c9a6a;
    --photo-stone: #8a8278;
  }
  * { box-sizing: border-box; margin: 0; padding: 0; }
  html, body { width: 1200px; height: 1200px; overflow: hidden; }
  body {
    background: linear-gradient(180deg, var(--bg-top), var(--bg-bottom));
    font-family: "Montserrat", Arial, sans-serif;
    color: var(--white);
    position: relative;
  }
  .package {
    position: absolute;
    left: 140px; top: 120px;
    display: grid;
    grid-template-columns: 300px 620px;
    grid-template-rows: 150px 780px;
  }
  .side-panel, .front-panel, .top-panel { box-shadow: 0 20px 40px rgba(0,0,0,.25); }

  /* Top panel */
  .top-panel {
    grid-column: 2; grid-row: 1;
    background: var(--panel-top);
    display: flex; align-items: center; justify-content: center;
  }
  .top-panel .brand { font-size: 20px; }

  /* Shared brand lockup */
  .brand {
    display: flex; align-items: center; gap: 10px;
    font-family: "Archivo", Arial, sans-serif;
    font-weight: 800; font-stretch: 125%;
    text-transform: uppercase; color: var(--white);
    line-height: 1.05;
  }
  .brand-dot { width: 30px; height: 30px; border-radius: 50%; background: var(--white); flex: none; }

  /* Side panel */
  .side-panel {
    grid-column: 1; grid-row: 2;
    background: var(--panel-dark);
    display: flex; flex-direction: column; align-items: center;
    padding-top: 80px;
    position: relative;
  }
  .side-panel .brand { font-size: 19px; }
  .promise-badge {
    margin-top: 40px;
    width: 100px; height: 100px; border-radius: 50%;
    border: 3px solid var(--white);
  }
  .box-contents {
    margin-top: 36px;
    list-style: none; text-align: center;
    font-family: "Archivo", Arial, sans-serif; font-weight: 700; font-stretch: 125%;
    font-size: 13px; line-height: 20px; letter-spacing: .5px;
  }
  .box-contents .heading { font-weight: 800; }
  .tagline {
    margin-top: 36px;
    font-family: "Archivo", Arial, sans-serif; font-weight: 800; font-stretch: 125%;
    font-size: 40px; line-height: 44px; text-align: center; letter-spacing: 1px;
  }
  .resistance-callout {
    position: absolute; left: 20px; right: 20px; bottom: 24px;
    height: 110px;
    background: var(--orange);
    display: flex; align-items: center; justify-content: center; text-align: center;
    font-family: "Archivo", Arial, sans-serif; font-weight: 800; font-stretch: 125%;
    font-size: 18px; line-height: 1.2; padding: 0 16px;
  }

  /* Front panel */
  .front-panel { grid-column: 2; grid-row: 2; position: relative; overflow: hidden; }
  .front-art { position: absolute; inset: 0; }
  .headline {
    position: absolute; left: 34px; top: 70px;
    font-family: "Archivo", Arial, sans-serif; font-stretch: 125%;
  }
  .headline .kicker { font-size: 24px; font-weight: 800; letter-spacing: 1px; }
  .headline .product { font-size: 54px; font-weight: 900; line-height: .98; margin-top: 4px; }
  .bonus-text {
    position: absolute; right: 15px; top: 6px; width: 150px; height: 150px;
    display: flex; flex-direction: column; align-items: center; justify-content: center;
    text-align: center; font-weight: 700; font-size: 14px; line-height: 1.2;
  }
  .bonus-text .bonus-title {
    font-family: "Archivo", Arial, sans-serif; font-stretch: 125%; font-weight: 900;
    font-size: 25px; border-bottom: 2px solid var(--white); margin-bottom: 4px; padding: 0 4px;
  }
  .front-brand { position: absolute; left: 36px; top: 560px; font-size: 20px; }
  .set-name {
    position: absolute; left: 36px; top: 650px;
    font-family: "Archivo", Arial, sans-serif; font-weight: 800; font-stretch: 125%;
    font-size: 17px; line-height: 1.25; color: var(--cream);
  }
</style>
</head>
<body>
  <main class="package">
    <section class="top-panel">
      <div class="brand"><span class="brand-dot"></span><span>Brisklane<br>Athletics</span></div>
    </section>

    <section class="side-panel">
      <div class="brand"><span class="brand-dot"></span><span>Brisklane<br>Athletics</span></div>
      <div class="promise-badge" role="img" aria-label="Brand promise badge"></div>
      <ul class="box-contents">
        <li class="heading">IN THE BOX</li>
        <li>x1 YELLOW - 2-4LB</li>
        <li>x1 GREEN - 4-6LB</li>
        <li>x1 BLUE - 10-12LB</li>
        <li>x1 RED - 15-20LB</li>
        <li>x1 BLACK - 25-30LB</li>
        <li>CARRY CASE</li>
        <li>E-BOOK</li>
      </ul>
      <p class="tagline">TONE<br>BURN<br>BUILD</p>
      <p class="resistance-callout">UP TO 75LBS<br>OF TOTAL<br>RESISTANCE</p>
    </section>

    <section class="front-panel">
      <svg class="front-art" viewBox="0 0 620 780" width="620" height="780">
        <defs>
          <linearGradient id="orangeSweep" x1="0" y1="0" x2="1" y2="0">
            <stop offset="0" stop-color="#d9481b"/>
            <stop offset="1" stop-color="#f29a2a"/>
          </linearGradient>
          <linearGradient id="orangeCorner" x1="0" y1="0" x2="1" y2="1">
            <stop offset="0" stop-color="#d9481b"/>
            <stop offset="1" stop-color="#f29a2a"/>
          </linearGradient>
          <linearGradient id="photoTones" x1="0" y1="0" x2="0" y2="1">
            <stop offset="0" stop-color="#d9dfe0"/>
            <stop offset=".45" stop-color="#8c9a6a"/>
            <stop offset="1" stop-color="#8a8278"/>
          </linearGradient>
        </defs>
        <rect class="workout-photo" x="0" y="0" width="620" height="780" fill="url(#photoTones)" role="img" aria-label="Photo of four people doing standing chest presses with resistance bands outdoors"/>
        <path class="header-band" d="M0 0 H620 V95 C430 140 220 190 0 262 Z" fill="url(#orangeSweep)"/>
        <path class="corner-band" d="M0 500 C60 630 190 730 360 780 H0 Z" fill="url(#orangeCorner)"/>
        <g class="bonus-badge-shape" transform="translate(525 81)">
          <rect x="-62" y="-62" width="124" height="124" fill="#d9481b"/>
          <rect x="-62" y="-62" width="124" height="124" fill="#d9481b" transform="rotate(22.5)"/>
          <rect x="-62" y="-62" width="124" height="124" fill="#d9481b" transform="rotate(45)"/>
          <rect x="-62" y="-62" width="124" height="124" fill="#d9481b" transform="rotate(67.5)"/>
        </g>
      </svg>

      <h1 class="headline">
        <span class="kicker">HIGH QUALITY</span><br>
        <span class="product">RESISTANCE<br>BANDS</span>
      </h1>

      <div class="bonus-text">
        <span class="bonus-title">BONUS</span>
        <span>Product and<br>Workout<br>Guide eBook</span>
      </div>

      <div class="brand front-brand"><span class="brand-dot"></span><span>Brisklane<br>Athletics</span></div>
      <p class="set-name">Brisklane Athletics<br>Resistance Band<br>Workout Set</p>
    </section>
  </main>
</body>
</html>
```